Brell Stone Company Business Cards

Front and Back Business Card - logo and text setup - cool design. I need workable photoshop or illustrator files so I can setup each employee card with design that is created
Updates

Hi everyone, thank you for the great entries. Please no more white and blue cards - there are so many already - black and silver only now please. thanks!

Target Market(s)

Construction Industry - Facility Managers

Industry/Entity Type

Construction

Contact Information for Business Card

I really like contemporary simplistic looks - clean neat....not opposed to seeing some black backrounds

Requirements
Must have
• Logo/website address with design on front only - www.brellstone-example.com (logo attached)
• Back:
• Name/Title/Company Address/Phone/email address
Nice to have
• Cool design
Should not have
• Nothing gimmicky like Fire or Water - since we are a Fire Protection company - it has all been done

```html
<!DOCTYPE html>
<html lang="en">
<head>
<meta charset="utf-8">
<title>Brell Stone Company Business Cards</title>
<link rel="stylesheet" href="https://fonts.googleapis.com/css2?family=Open+Sans:wght@400;600;700;800&display=swap">
<style>
  :root {
    --stage: #1c1c1e;
    --metal-dark: #141416;
    --metal-mid: #2a2a2d;
    --metal-light: #4a4a4f;
    --brand-blue: #0a24a0;
    --brand-red: #ff2222;
    --text-white: #ffffff;
    --text-soft: #e6e6e6;
  }
  html, body {
    margin: 0;
    padding: 0;
    width: 1200px;
    height: 960px;
    overflow: hidden;
    background: var(--stage);
    font-family: "Open Sans", sans-serif;
  }
  .canvas {
    position: relative;
    width: 1200px;
    height: 960px;
  }
  .card {
    position: absolute;
    left: 320px;
    width: 560px;
    height: 320px;
    border-radius: 4px;
    overflow: hidden;
    background:
      linear-gradient(100deg, transparent 30%, rgba(255,255,255,0.08) 48%, rgba(255,255,255,0.16) 55%, rgba(255,255,255,0.06) 62%, transparent 78%),
      repeating-linear-gradient(0deg, rgba(255,255,255,0.025) 0 1px, transparent 1px 3px),
      linear-gradient(180deg, var(--metal-mid), var(--metal-dark));
    box-shadow: 0 10px 30px rgba(0,0,0,0.5);
  }
  .card--front { top: 100px; }
  .card--back { top: 540px; }

  .wordmark {
    margin: 0;
    font-weight: 800;
    color: var(--brand-red);
    letter-spacing: -0.5px;
    line-height: 1;
  }
  .card--front .wordmark {
    position: absolute;
    top: 110px;
    width: 100%;
    text-align: center;
    font-size: 54px;
  }
  .front-website {
    position: absolute;
    top: 196px;
    width: 100%;
    text-align: center;
    color: var(--text-soft);
    font-size: 15px;
    letter-spacing: 4px;
  }

  .card--back .wordmark {
    position: absolute;
    top: 30px;
    left: 32px;
    font-size: 36px;
  }
  .address {
    position: absolute;
    top: 92px;
    left: 34px;
    margin: 0;
    color: var(--text-white);
    font-size: 14px;
    line-height: 1.45;
    font-style: normal;
  }
  .back-shapes {
    position: absolute;
    inset: 0;
  }
  .contact-list {
    position: absolute;
    top: 168px;
    left: 28px;
    margin: 0;
    padding: 0;
    list-style: none;
    color: var(--text-white);
    font-size: 14px;
  }
  .contact-list li {
    display: flex;
    align-items: center;
    gap: 9px;
    height: 24px;
  }
  .contact-icon { width: 13px; height: 13px; flex: none; }
  .name-tab {
    position: absolute;
    left: 336px;
    top: 205px;
    width: 180px;
    text-align: center;
    color: var(--text-white);
  }
  .person-name {
    margin: 0;
    font-size: 17px;
    font-weight: 700;
    line-height: 1.2;
  }
  .person-title {
    margin: 0;
    font-size: 15px;
    line-height: 1.3;
  }
</style>
</head>
<body>
<main class="canvas">

  <section class="card card--front" aria-label="Business card front">
    <p class="wordmark">Brell Stone</p>
    <p class="front-website">www.brellstone-example.com</p>
  </section>

  <section class="card card--back" aria-label="Business card back">
    <svg class="back-shapes" width="560" height="320" viewBox="0 0 560 320" aria-hidden="true">
      <path d="M0 150 H326 C344 150 338 236 362 236 H560 V320 H0 Z" fill="var(--brand-blue)"/>
      <rect x="334" y="198" width="184" height="62" rx="16" fill="var(--brand-red)"/>
    </svg>

    <p class="wordmark">Brell Stone</p>
    <address class="address">48 Harbor Works Lane<br>Millbrook, NY 10000</address>

    <ul class="contact-list">
      <li>
        <svg class="contact-icon" viewBox="0 0 16 16" aria-hidden="true"><path d="M3 1 L6 1 L7 5 L5 6.5 C6 9 7 10 9.5 11 L11 9 L15 10 L15 13 C15 14 14 15 13 15 C6 15 1 10 1 3 C1 2 2 1 3 1 Z" fill="var(--brand-red)"/></svg>
        <span>(555) 014-2290</span>
      </li>
      <li>
        <svg class="contact-icon" viewBox="0 0 16 16" aria-hidden="true"><rect x="1" y="3" width="14" height="10" fill="var(--brand-red)"/><path d="M1 3 L8 9 L15 3" fill="none" stroke="var(--brand-blue)" stroke-width="1.4"/></svg>
        <span>info@brellstone-example.com</span>
      </li>
      <li>
        <svg class="contact-icon" viewBox="0 0 16 16" aria-hidden="true"><circle cx="8" cy="8" r="6.5" fill="none" stroke="var(--brand-red)" stroke-width="1.5"/><ellipse cx="8" cy="8" rx="3" ry="6.5" fill="none" stroke="var(--brand-red)" stroke-width="1.2"/><path d="M1.5 8 H14.5" stroke="var(--brand-red)" stroke-width="1.2"/></svg>
        <span>www.brellstone-example.com</span>
      </li>
    </ul>

    <div class="name-tab">
      <p class="person-name">Dana Whitlow</p>
      <p class="person-title">President</p>
    </div>
  </section>

</main>
</body>
</html>
```